ORLA - Óptica Médica - web design and concept

Website concept - Create and develop our website design and structure. ORLA is an optical store chain, and we are looking to establish our web and digital concept. In attachment there are several pictures about our stores and our logo.

The website structure should be user friendly. Colors should be light and the design as simple and minimalist as possible. There are different variations of the logothat can be used, check the file.

The website will include optical collections and sun collections as an online store. Also, a medical menu should be considered in order for clients to schedule optometry appointments. There should also be a menu for client assistance where the clients can read about glass maintenance in our workshop.
Updates

Low design quality

Number of Pages Required

5+ page

Font styles to use
Serif
Sans Serif

Requirements
Must have
• Must be user-friendly and minimalist.
• Please USE PICTURES FROM THE BRANDS we sell: MERUN, BOSKA, PNW, KOLE, BAMPE
Nice to have
• Nice to inspire: ZEK glasses (see website https://ch.shopzek.com/en/)
• Nice to inspire: https://merun-eyewear.com/
• Nice to ispire: https://www.pnwglobe.com/en/
Should not have
• Hysteric colors and shapes

```html
<!DOCTYPE html>
<html lang="en">
<head>
<meta charset="utf-8">
<title>ORLA Óptica Médica — Desktop and Mobile Home</title>
<link href="https://fonts.googleapis.com/css2?family=Alegreya:wght@400;500;700&family=Roboto:wght@400;500;700&display=swap" rel="stylesheet">
<style>
:root{
  --gold:#d4a94a;
  --gold-dark:#b98f33;
  --ink:#1c1c1c;
  --muted:#6b6b6b;
  --paper:#ffffff;
  --mist:#f3f3f3;
  --stage:#ececec;
  --night:#050505;
  --serif:"Alegreya", Georgia, serif;
  --sans:"Roboto", Arial, sans-serif;
}
*{box-sizing:border-box;margin:0;padding:0}
html,body{width:1200px;height:3947px;overflow:hidden}
body{background:var(--stage);font-family:var(--sans);color:var(--ink);position:relative}
.abs{position:absolute}
.page{position:absolute;background:var(--paper);overflow:hidden;box-shadow:0 2px 14px rgba(0,0,0,.12)}
.desktop{left:58px;top:26px;width:774px;height:1685px}
.mobile{left:887px;top:118px;width:260px;height:3685px}
.wordmark{font-family:var(--serif);font-weight:500;color:var(--gold);letter-spacing:.18em}
.photo{position:absolute}
.btn{position:absolute;background:var(--gold);color:#fff;font:500 8px/1 var(--sans);letter-spacing:.06em;text-transform:uppercase;display:flex;align-items:center;justify-content:center}
.btn.light{background:rgba(255,255,255,.25);border:1px solid rgba(255,255,255,.6)}
.title{font-family:var(--serif);font-weight:500;color:var(--gold);letter-spacing:.03em}
.sub{font-family:var(--serif);font-weight:700;color:var(--ink)}
.small{font-size:7px;line-height:1.5;color:var(--muted)}
.nav{display:flex;gap:22px;font:500 8px var(--sans);color:var(--ink)}
.feature{position:absolute;text-align:center;font:500 7.5px var(--sans);color:var(--ink)}
.feature svg{display:block;margin:0 auto 5px}
.band-gold{position:absolute;left:0;right:0;background:var(--gold)}
.band-gold .title,.band-gold .sub{color:#fff;text-align:center;position:absolute;left:0;right:0}
.band-gold .para{position:absolute;color:#fff;font-size:7px;line-height:1.6;text-align:center}
.band-mist{position:absolute;left:0;right:0;background:var(--mist)}
.product{position:absolute;text-align:center}
.product .mark{width:12px;height:12px;border-radius:50%;border:1.5px solid var(--gold);margin:0 auto 6px}
.product .name{font:700 7px var(--sans);letter-spacing:.05em}
.product .frame{height:34px;margin:8px auto;background:linear-gradient(#fafafa,#e2e2e2)}
.product .price{font-size:6.5px;color:var(--muted)}
.brands{position:absolute;left:0;right:0;background:#fff;display:flex;align-items:center;justify-content:space-around}
.brand{font-family:var(--sans);font-weight:700;font-size:12px;letter-spacing:.12em;color:var(--ink)}
.footer{position:absolute;left:0;right:0;background:var(--night);color:#fff}
.footer h4{font:500 8px var(--sans);color:#fff}
.footer li{list-style:none;font-size:6.5px;color:#9b9b9b;line-height:2}
.socials{display:flex;gap:4px}
.socials span{width:12px;height:12px;display:block;border-radius:2px}
.copy{position:absolute;left:0;right:0;text-align:center;font-size:6px;color:#8a8a8a}
</style>
</head>
<body>

<!-- DESKTOP HOME -->
<section class="page desktop" aria-label="Desktop home page">
  <header>
    <div class="abs" style="left:112px;top:28px;width:100px;text-align:center">
      <div class="wordmark" style="font-size:30px">ORLA</div>
    </div>
    <nav class="nav abs" style="left:245px;top:18px">
      <span>Home</span><span>About Us</span><span>Products</span><span>Contact Us</span><span>Blogs</span><span>Users</span><span>Sign In</span><span>Language</span>
    </nav>
    <div class="photo" role="img" aria-label="Interior of an optical store with wooden counter and frame displays" style="left:384px;top:47px;width:390px;height:295px;background:linear-gradient(160deg,#5f5d57 0%,#8d8377 45%,#b58a52 75%,#e4e0d8 100%)"></div>
    <h1 class="title abs" style="left:40px;top:180px;font-size:34px">ORLA OPTICA</h1>
    <p class="sub abs" style="left:40px;top:222px;font-size:15px">Our Priority Is Your Visual Health</p>
    <div class="btn" style="left:40px;top:262px;width:74px;height:24px">Learn more</div>
  </header>

  <div class="abs" style="left:0;top:342px;width:774px;height:76px;border-top:1px solid #e6e6e6">
    <div class="feature" style="left:20px;top:14px;width:130px">
      <svg width="18" height="18" viewBox="0 0 20 20"><path d="M10 1 L18 4 V9 C18 14 14 17 10 19 C6 17 2 14 2 9 V4 Z" fill="none" stroke="#d4a94a" stroke-width="1.6"/><path d="M6 10 L9 13 L14 7" fill="none" stroke="#d4a94a" stroke-width="1.6"/></svg>Orla Childhood Guarantee</div>
    <div class="feature" style="left:170px;top:14px;width:130px">
      <svg width="18" height="18" viewBox="0 0 20 20"><circle cx="10" cy="10" r="8" fill="none" stroke="#d4a94a" stroke-width="1.6"/><path d="M6 10 L9 13 L14 7" fill="none" stroke="#d4a94a" stroke-width="1.6"/></svg>Orla Accident Warranty</div>
    <div class="feature" style="left:320px;top:14px;width:130px">
      <svg width="18" height="18" viewBox="0 0 20 20"><rect x="4" y="9" width="12" height="9" rx="1" fill="none" stroke="#d4a94a" stroke-width="1.6"/><path d="M7 9 V6 A3 3 0 0 1 13 6 V9" fill="none" stroke="#d4a94a" stroke-width="1.6"/></svg>Orla Security</div>
    <div class="feature" style="left:470px;top:14px;width:130px">
      <svg width="20" height="18" viewBox="0 0 22 20"><path d="M1 10 C5 3 17 3 21 10 C17 17 5 17 1 10 Z" fill="none" stroke="#d4a94a" stroke-width="1.6"/><circle cx="11" cy="10" r="3.5" fill="#d4a94a"/></svg>Orla Vision</div>
    <div class="feature" style="left:620px;top:14px;width:140px">
      <svg width="18" height="18" viewBox="0 0 20 20"><circle cx="10" cy="10" r="6" fill="none" stroke="#d4a94a" stroke-width="3" stroke-dasharray="3 2"/><circle cx="10" cy="10" r="2.5" fill="none" stroke="#d4a94a" stroke-width="1.6"/></svg>Manufacturer's Warranty</div>
  </div>

  <section class="band-gold" style="top:420px;height:290px">
    <h2 class="title" style="top:42px;font-size:30px">ORLA OPTICA</h2>
    <p class="sub" style="top:82px;font-size:12px">Our Priority Is Your Visual Health</p>
    <p class="para" style="left:160px;width:454px;top:106px">ORLA OPTICA opens its doors with a clear purpose: to take care of you. Our priority is your visual health, and for this reason we have the best professionals and the most competitive products in our eyes.</p>
    <div class="btn light" style="left:210px;top:170px;width:64px;height:22px">Learn more</div>
    <div class="btn light" style="left:290px;top:170px;width:64px;height:22px">Shop now</div>
  </section>

  <section class="band-mist" style="top:710px;height:632px"></section>
  <div class="photo" role="img" aria-label="Portrait of a woman in a yellow hat wearing blue frames" style="left:163px;top:658px;width:213px;height:223px;background:linear-gradient(150deg,#e7b63b 0%,#d9a24a 40%,#8f6a4c 70%,#f1ede6 100%)"></div>
  <p class="abs" style="left:395px;top:685px;font-size:7px;color:#fff">Follow us on our channel</p>
  <div class="photo" role="img" aria-label="Portrait of a young woman wearing dark frames" style="left:395px;top:710px;width:211px;height:232px;background:linear-gradient(160deg,#d6cfc6 0%,#a58f7d 45%,#6e5c50 80%,#cfc6bb 100%)"></div>
  <p class="abs" style="left:163px;top:902px;font:700 7px var(--sans)">About Orla Medina</p>
  <h2 class="abs sub" style="left:163px;top:916px;font-size:26px;font-weight:500">About Orla</h2>
  <p class="abs small" style="left:163px;top:956px;width:210px">ORLA OPTICA opens its doors with a clear purpose: to take care of you. Our priority is your visual health.</p>

  <div class="product" style="left:100px;top:1090px;width:145px">
    <div class="mark"></div>
    <div class="name">GRADUATED FRAME</div>
    <div class="frame" role="img" aria-label="Black optical frame" style="width:100px"></div>
    <div class="price">€ 79.90 &nbsp;|&nbsp; 2 Options available</div>
    <div class="btn" style="position:relative;margin:12px auto 0;width:68px;height:20px">Shop now</div>
  </div>
  <div class="photo" role="img" aria-label="Woman holding glasses against a yellow wall" style="left:255px;top:1047px;width:128px;height:116px;background:linear-gradient(150deg,#f1c21e,#d78a3c)"></div>
  <div class="photo" role="img" aria-label="Hand holding a pair of glasses" style="left:388px;top:1047px;width:128px;height:116px;background:linear-gradient(150deg,#eceae6,#b9b4ad)"></div>
  <div class="photo" role="img" aria-label="Woman in round glasses, blue tones" style="left:255px;top:1168px;width:128px;height:116px;background:linear-gradient(150deg,#4d5b6c,#9aa5b1)"></div>
  <div class="photo" role="img" aria-label="Woman smiling in tortoise frames" style="left:388px;top:1168px;width:128px;height:116px;background:linear-gradient(150deg,#dcd3c5,#8f7b68)"></div>
  <div class="product" style="left:530px;top:1090px;width:145px">
    <div class="mark"></div>
    <div class="name">GRADUATED FRAME</div>
    <div class="frame" role="img" aria-label="Black optical frame" style="width:100px"></div>
    <div class="price">€ 79.90 &nbsp;|&nbsp; 2 Options available</div>
    <div class="btn" style="position:relative;margin:12px auto 0;width:68px;height:20px">Shop now</div>
  </div>

  <div class="brands" style="top:1342px;height:92px;padding:0 80px">
    <span class="brand">NORVE</span><span class="brand">ELSAN</span><span class="brand">VIREO</span><span class="brand">CALDA</span><span class="brand">TORMA</span>
  </div>

  <footer class="footer" style="top:1434px;height:251px">
    <div class="abs" style="left:70px;top:40px;width:100px;text-align:center"><div class="wordmark" style="font-size:26px">ORLA</div></div>
    <h4 class="abs" style="left:210px;top:30px;width:150px">Are you going to miss the best posts of the blog?</h4>
    <div class="photo" role="img" aria-label="Glasses resting on a desk" style="left:210px;top:58px;width:150px;height:60px;background:linear-gradient(150deg,#2a3b4d,#7a8a96)"></div>
    <h4 class="abs" style="left:430px;top:30px">Navigation</h4>
    <ul class="abs" style="left:432px;top:44px"><li>Home</li><li>About Us</li><li>Products</li><li>Contact Us</li><li>Blogs</li><li>Users</li></ul>
    <h4 class="abs" style="left:550px;top:30px">Follow us</h4>
    <div class="socials abs" style="left:550px;top:46px"><span style="background:#3b5998"></span><span style="background:#1da1f2"></span><span style="background:#dd4b39"></span><span style="background:#0077b5"></span><span style="background:#3b80c4"></span></div>
    <div class="abs" style="left:20px;right:20px;top:205px;border-top:1px solid #222"></div>
    <p class="copy" style="top:222px">Copyright © 2019 Orla. All Rights Reserved</p>
  </footer>
</section>

<!-- MOBILE HOME -->
<section class="page mobile" aria-label="Mobile home page">
  <div class="abs" style="left:0;right:0;top:40px;text-align:center"><div class="wordmark" style="font-size:24px">ORLA</div></div>
  <p class="abs" style="left:10px;top:134px;font:500 7px var(--sans)">Sign In &nbsp;&nbsp; Language</p>
  <svg class="abs" style="left:238px;top:134px" width="12" height="8" viewBox="0 0 12 8"><path d="M0 1H12M0 4H12M0 7H12" stroke="#1c1c1c" stroke-width="1.2"/></svg>
  <h1 class="title abs" style="left:10px;top:214px;font-size:30px">ORLA OPTICA</h1>
  <p class="sub abs" style="left:10px;top:256px;font-size:13px">Our Priority Is Your Visual Health</p>
  <div class="btn" style="left:10px;top:306px;width:72px;height:24px">Learn more</div>
  <div class="photo" role="img" aria-label="Interior of an optical store with wooden counter" style="left:0;top:408px;width:260px;height:263px;background:linear-gradient(160deg,#5f5d57 0%,#8d8377 45%,#b58a52 75%,#e4e0d8 100%)"></div>

  <div class="feature" style="left:10px;top:700px;width:110px"><svg width="18" height="18" viewBox="0 0 20 20"><path d="M10 1 L18 4 V9 C18 14 14 17 10 19 C6 17 2 14 2 9 V4 Z" fill="none" stroke="#d4a94a" stroke-width="1.6"/></svg>Orla Childhood Guarantee</div>
  <div class="feature" style="left:140px;top:700px;width:110px"><svg width="18" height="18" viewBox="0 0 20 20"><circle cx="10" cy="10" r="8" fill="none" stroke="#d4a94a" stroke-width="1.6"/><path d="M6 10 L9 13 L14 7" fill="none" stroke="#d4a94a" stroke-width="1.6"/></svg>Orla Accident Warranty</div>
  <div class="feature" style="left:10px;top:770px;width:110px"><svg width="18" height="18" viewBox="0 0 20 20"><rect x="4" y="9" width="12" height="9" rx="1" fill="none" stroke="#d4a94a" stroke-width="1.6"/><path d="M7 9 V6 A3 3 0 0 1 13 6 V9" fill="none" stroke="#d4a94a" stroke-width="1.6"/></svg>Orla Security</div>
  <div class="feature" style="left:140px;top:770px;width:110px"><svg width="20" height="18" viewBox="0 0 22 20"><path d="M1 10 C5 3 17 3 21 10 C17 17 5 17 1 10 Z" fill="none" stroke="#d4a94a" stroke-width="1.6"/><circle cx="11" cy="10" r="3.5" fill="#d4a94a"/></svg>Orla Vision</div>
  <div class="feature" style="left:75px;top:840px;width:110px"><svg width="18" height="18" viewBox="0 0 20 20"><circle cx="10" cy="10" r="6" fill="none" stroke="#d4a94a" stroke-width="3" stroke-dasharray="3 2"/></svg>Manufacturer's Warranty</div>

  <section class="band-gold" style="top:900px;height:218px">
    <h2 class="title" style="top:40px;font-size:26px">ORLA OPTICA</h2>
    <p class="sub" style="top:76px;font-size:11px">Our Priority Is Your Visual Health</p>
    <p class="para" style="left:16px;width:228px;top:100px">ORLA OPTICA opens its doors with a clear purpose: to take care of you. Our priority is your visual health, and for this we have the best professionals and the most competitive products.</p>
    <div class="btn light" style="left:60px;top:160px;width:62px;height:20px">Learn more</div>
    <div class="btn light" style="left:138px;top:160px;width:62px;height:20px">Shop now</div>
  </section>

  <div class="photo" role="img" aria-label="Portrait of a woman in a yellow hat wearing blue frames" style="left:16px;top:1144px;width:229px;height:245px;background:linear-gradient(150deg,#e7b63b 0%,#d9a24a 40%,#8f6a4c 70%,#f1ede6 100%)"></div>
  <p class="abs" style="left:16px;top:1408px;font:700 7px var(--sans)">About Orla Medina</p>
  <h2 class="abs sub" style="left:16px;top:1422px;font-size:24px;font-weight:500">About Orla</h2>
  <p class="abs small" style="left:16px;top:1460px;width:228px">ORLA OPTICA opens its doors with a clear purpose: to take care of you. Our priority is your visual health.</p>
  <p class="abs" style="left:16px;top:1525px;font:500 7px var(--sans)">Follow us on our channel</p>
  <div class="photo" role="img" aria-label="Portrait of a young woman wearing dark frames" style="left:16px;top:1560px;width:229px;height:250px;background:linear-gradient(160deg,#d6cfc6 0%,#a58f7d 45%,#6e5c50 80%,#cfc6bb 100%)"></div>

  <section class="band-mist" style="top:1830px;height:997px"></section>
  <div class="product" style="left:55px;top:1850px;width:150px">
    <div class="mark"></div>
    <div class="name">GRADUATED FRAME</div>
    <div class="frame" role="img" aria-label="Black optical frame" style="width:100px"></div>
    <div class="price">€ 79.90 &nbsp;|&nbsp; 2 Options available</div>
    <div class="btn" style="position:relative;margin:12px auto 0;width:68px;height:20px">Shop now</div>
  </div>
  <div class="photo" role="img" aria-label="Woman holding glasses against a yellow wall" style="left:47px;top:2064px;width:161px;height:124px;background:linear-gradient(150deg,#f1c21e,#d78a3c)"></div>
  <div class="photo" role="img" aria-label="Hand holding a pair of glasses" style="left:47px;top:2191px;width:161px;height:124px;background:linear-gradient(150deg,#eceae6,#b9b4ad)"></div>
  <div class="photo" role="img" aria-label="Woman in round glasses, blue tones" style="left:47px;top:2318px;width:161px;height:124px;background:linear-gradient(150deg,#4d5b6c,#9aa5b1)"></div>
  <div class="photo" role="img" aria-label="Woman smiling in tortoise frames" style="left:47px;top:2445px;width:161px;height:124px;background:linear-gradient(150deg,#dcd3c5,#8f7b68)"></div>
  <div class="product" style="left:55px;top:2600px;width:150px">
    <div class="mark"></div>
    <div class="name">GRADUATED FRAME</div>
    <div class="frame" role="img" aria-label="Black optical frame" style="width:100px"></div>
    <div class="price">€ 79.90 &nbsp;|&nbsp; 2 Options available</div>
    <div class="btn" style="position:relative;margin:12px auto 0;width:68px;height:20px">Shop now</div>
  </div>

  <div class="brands" style="top:2827px;height:200px;flex-wrap:wrap;padding:30px 30px;align-content:space-around">
    <span class="brand" style="width:50%;text-align:center">NORVE</span><span class="brand" style="width:50%;text-align:center">ELSAN</span>
    <span class="brand" style="width:50%;text-align:center">VIREO</span><span class="brand" style="width:50%;text-align:center">CALDA</span>
    <span class="brand" style="width:100%;text-align:center">TORMA</span>
  </div>

  <footer class="footer" style="top:3058px;height:627px">
    <div class="abs" style="left:0;right:0;top:50px;text-align:center"><div class="wordmark" style="font-size:26px">ORLA</div></div>
    <h4 class="abs" style="left:0;right:0;top:150px;text-align:center">Are you going to miss the best posts of the blog?</h4>
    <div class="photo" role="img" aria-label="Glasses resting on a desk" style="left:48px;top:170px;width:164px;height:62px;background:linear-gradient(150deg,#2a3b4d,#7a8a96)"></div>
    <h4 class="abs" style="left:48px;top:302px">Navigation</h4>
    <ul class="abs" style="left:50px;top:318px"><li>Home</li><li>About Us</li><li>Products</li><li>Contact Us</li><li>Blogs</li><li>Users</li></ul>
    <h4 class="abs" style="left:48px;top:460px">Follow us</h4>
    <div class="socials abs" style="left:48px;top:478px"><span style="background:#3b5998"></span><span style="background:#1da1f2"></span><span style="background:#dd4b39"></span><span style="background:#0077b5"></span><span style="background:#3b80c4"></span></div>
    <div class="abs" style="left:16px;right:16px;top:560px;border-top:1px solid #222"></div>
    <p class="copy" style="top:585px">Copyright © 2019 Orla. All Rights Reserved</p>
  </footer>
</section>

</body>
</html>
```